Local Flower Farm Needs Business Card Design

I need business cards designed for a flower farm based in Eudora, Kansas.
Business Info:
We are a local cut flower farm located in Eudora, Kansas, founded by Corinne Haldwick. What started as a passion for agriculture and search for more joy in daily life has blossomed into a small business dedicated to providing the community with beautiful, fresh, and sustainable flowers. We specialize in local, seasonal blooms, ensuring that every petal reflects the care and dedication we pour into our craft. Our mission is to deliver the highest quality flowers directly to our customers through local farmers markets and to florists who share our commitment to sustainability. Join us in celebrating the beauty of nature, one bloom at a time!
Contact Details:
Corinne Haldwick
Owner
Phone 913-555-0147
Facebook: Rosalind Thorpe Gardens
Instagram: @RosalindThorpeGardens
Website: RosalindThorpeGardens.example
Target Market(s)
Wholesale to Florists and Direct to Consumer via Farmers Market
Industry/Entity Type
Florist, Farm
Contact Information for Business Card
Name, Contact Info, Logo
Look and feel
Each slider illustrates characteristics of the customer's brand and the style your logo design should communicate.

```html
<!DOCTYPE html>
<html lang="en">
<head>
<meta charset="utf-8">
<title>Rosalind Thorpe Gardens — Business Card</title>
<link href="https://fonts.googleapis.com/css2?family=Montserrat:wght@400;500;700&display=swap" rel="stylesheet">
<style>
  :root {
    --forest: #0a2328;
    --forest-deep: #061d22;
    --paper: #f1f1f1;
    --paper-soft: #e6e6e6;
    --ink: #0c2a2f;
    --backdrop: #d9dcda;
  }
  * { box-sizing: border-box; margin: 0; padding: 0; }
  html, body {
    width: 1200px; height: 1200px; overflow: hidden;
    background: var(--backdrop);
    font-family: "Montserrat", sans-serif;
  }
  .sheet { position: relative; width: 1200px; height: 1200px; }
  .card {
    position: absolute; left: 220px; width: 760px; height: 434px;
    border-radius: 4px; overflow: hidden;
    box-shadow: 0 10px 28px rgba(0,0,0,0.18);
  }
  .card--front { top: 150px; background: linear-gradient(180deg, var(--paper), var(--paper-soft)); }
  .card--back { top: 644px; background: linear-gradient(160deg, var(--forest), var(--forest-deep)); }

  .holder {
    position: absolute; left: 46px; top: 58px;
    display: flex; align-items: center; color: var(--ink);
  }
  .holder__name { font-weight: 700; font-size: 27px; letter-spacing: 0.2px; }
  .holder__divider { width: 2px; height: 28px; background: var(--ink); margin: 0 16px; }
  .holder__role { font-weight: 400; font-size: 21px; letter-spacing: 0.5px; }

  .band {
    position: absolute; left: 0; right: 0; top: 189px; bottom: 0;
    background: linear-gradient(170deg, var(--forest), var(--forest-deep));
  }
  .contacts { position: absolute; left: 46px; top: 58px; list-style: none; }
  .contacts li {
    display: flex; align-items: center; height: 34px;
    color: var(--paper); font-size: 19px; font-weight: 400; letter-spacing: 0.2px;
  }
  .contacts svg { width: 24px; height: 24px; margin-right: 12px; flex: none; }

  .brand-panel {
    position: absolute; right: 12px; top: 0; width: 220px; height: 245px;
    background: var(--paper); border-radius: 0 0 0 22px;
    display: flex; flex-direction: column; align-items: center; justify-content: center;
    color: var(--ink); text-align: center;
  }
  .brand-panel__name {
    font-weight: 500; font-size: 22px; line-height: 1.35; letter-spacing: 2px; text-transform: uppercase;
  }

  .emblem {
    position: absolute; left: 50%; top: 82px; transform: translateX(-50%);
    display: flex; flex-direction: column; align-items: center; color: var(--paper);
  }
  .emblem__ring { width: 70px; height: 70px; border: 1.5px solid var(--paper); border-radius: 50%; margin-bottom: 18px; }
  .emblem__name { font-weight: 500; font-size: 22px; letter-spacing: 4px; text-transform: uppercase; white-space: nowrap; }

  .social {
    position: absolute; left: 0; right: 0; top: 368px;
    display: flex; justify-content: center; align-items: center;
    color: var(--paper); font-size: 19px; letter-spacing: 0.3px;
  }
  .social__dot { width: 24px; height: 24px; border-radius: 50%; background: var(--paper); margin-right: 12px; }
</style>
</head>
<body>
<main class="sheet">
  <section class="card card--front">
    <div class="holder">
      <span class="holder__name">Corinne Haldwick</span>
      <span class="holder__divider"></span>
      <span class="holder__role">Owner</span>
    </div>
    <div class="band">
      <ul class="contacts">
        <li>
          <svg viewBox="0 0 24 24"><circle cx="12" cy="12" r="12" fill="#f1f1f1"/><path d="M8.3 6.5l2 2.2-1.2 1.4c.8 1.7 2 2.9 3.7 3.8l1.4-1.2 2.2 2-1.3 1.9c-3.9-.6-7.2-3.8-7.8-7.8z" fill="#0a2328"/></svg>
          913-555-0147
        </li>
        <li>
          <svg viewBox="0 0 24 24"><circle cx="12" cy="12" r="12" fill="#f1f1f1"/><rect x="6.5" y="8" width="11" height="8" rx="1" fill="#0a2328"/><path d="M7 8.6l5 3.8 5-3.8" fill="none" stroke="#f1f1f1" stroke-width="1.1"/></svg>
          corinne@rosalindthorpegardens.example
        </li>
        <li>
          <svg viewBox="0 0 24 24"><circle cx="12" cy="12" r="12" fill="#f1f1f1"/><circle cx="12" cy="12" r="6" fill="none" stroke="#0a2328" stroke-width="1.4"/><ellipse cx="12" cy="12" rx="2.5" ry="6" fill="none" stroke="#0a2328" stroke-width="1.2"/><path d="M6 12h12" stroke="#0a2328" stroke-width="1.2"/></svg>
          www.rosalindthorpegardens.example
        </li>
        <li>
          <svg viewBox="0 0 24 24"><circle cx="12" cy="12" r="12" fill="#f1f1f1"/></svg>
          @RosalindThorpeGardens
        </li>
      </ul>
      <div class="brand-panel">
        <span class="brand-panel__name">Rosalind<br>Thorpe<br>Gardens</span>
      </div>
    </div>
  </section>

  <section class="card card--back">
    <div class="emblem">
      <span class="emblem__ring"></span>
      <span class="emblem__name">Rosalind Thorpe Gardens</span>
    </div>
    <div class="social">
      <span class="social__dot"></span>
      @RosalindThorpeGardens
    </div>
  </section>
</main>
</body>
</html>
```